Velmora Systems Website

Website design for our company: Velmora Systems.
The website should look fresh and IT focused. Please have a look at http://www.velmorasystems.example.au/ for our current design. We want something fresh and new, professional looking, in WordPress so we can easily make changes.

It Company

```html
<!DOCTYPE html>
<html lang="en">
<head>
<meta charset="utf-8">
<title>Velmora Systems</title>
<link href="https://fonts.googleapis.com/css2?family=Open+Sans:wght@400;600;700&display=swap" rel="stylesheet">
<style>
:root{
  --blue:#0b62b4;
  --band:#0f6fbf;
  --green:#1aa84c;
  --navy:#0a1a2c;
  --ink:#333;
  --muted:#555;
  --line:#bfbfbf;
  --foot:#3b3b3b;
  --footbox:#474747;
}
*{box-sizing:border-box;margin:0;padding:0}
html,body{width:952px;height:1200px;overflow:hidden;background:#fff}
body{position:relative;font-family:Arial,Helvetica,sans-serif;color:var(--ink)}
.abs{position:absolute}
.head{position:absolute;left:0;top:0;width:952px;height:94px;background:linear-gradient(#fff,#f1f1f1);border-top:2px solid var(--blue);border-bottom:1px solid #ddd}
.brand{position:absolute;display:flex;align-items:center;gap:8px;font-family:'Open Sans',sans-serif;font-weight:700;font-size:17px;color:var(--green)}
.brand i{display:block;width:22px;height:22px;background:var(--green)}
.search{left:520px;top:27px;width:147px;height:21px;border:1px solid #ccc;background:#fff;font:italic 10px Arial,sans-serif;color:#666;padding:4px 7px}
.search svg{position:absolute;right:5px;top:4px}
.call{left:688px;top:22px;font-family:'Open Sans',sans-serif}
.call small{display:block;font-size:9px;color:#333;margin-left:30px}
.call b{display:block;font-size:16px;font-weight:400;color:#222;margin-left:30px;line-height:18px}
.call svg{position:absolute;left:0;top:3px}
.nav{left:309px;top:64px;display:flex;font-family:'Open Sans',sans-serif;font-size:11px;color:#333}
.nav span{padding:0 12px;border-left:1px solid #bbb;line-height:13px}
.nav span:first-child{border:none;color:var(--green)}
.hero{left:0;top:94px;width:952px;height:333px;background:var(--navy)}
.hero-photo{position:absolute;left:133px;top:0;width:679px;height:333px;background:linear-gradient(90deg,#2a2f36 0%,#3c4650 40%,#9c8a80 75%,#c9b5a8 100%)}
.arrow{position:absolute;top:153px;width:28px;height:28px;border-radius:50%;background:#1d1d1d}
.dots{position:absolute;left:412px;top:224px;display:flex;gap:13px}
.dots i{display:block;width:8px;height:8px;border-radius:50%;background:var(--green)}
.caption{position:absolute;left:0;top:295px;width:952px;height:38px;background:rgba(15,111,191,.92);color:#fff;font-family:'Open Sans',sans-serif;font-size:18px;text-align:center;line-height:38px}
h2{position:absolute;font-family:'Open Sans',sans-serif;font-weight:600;font-size:16px;color:var(--blue)}
.rule{position:absolute;border-top:1px dashed var(--line);height:0}
.svc{position:absolute;top:502px;width:130px;text-align:center}
.svc h3{font-family:'Open Sans',sans-serif;font-weight:600;font-size:11px;color:#333;height:18px}
.svc.on h3{color:var(--green)}
.ring{width:96px;height:96px;margin:8px auto 0;border-radius:50%;background:radial-gradient(#fafafa 55%,#e2e2e2);border:2px solid #e6e6e6;display:flex;align-items:center;justify-content:center}
.svc.on .ring{background:#fff;border:4px solid var(--green)}
.svc p{font-size:9.5px;line-height:14px;color:#333;margin-top:18px}
.about-img{left:140px;top:759px;width:202px;height:93px;background:linear-gradient(120deg,#dde6ee,#9aa6b2 50%,#2d3440)}
.copy{position:absolute;font-size:8.5px;line-height:12.7px;color:#333;text-align:justify}
.more{position:absolute;font-size:9px;font-weight:700;color:var(--green)}
.quote{position:absolute;left:372px;width:208px;font-size:9.5px;line-height:14.6px;color:#444}
.quote .by{text-align:right;font-weight:700;font-size:8.5px;color:#555;line-height:11px}
.field{position:absolute;left:609px;width:203px;height:22px;border:1px solid #ccc;background:#fff;font:italic 9px Arial,sans-serif;color:#777;padding:5px 8px;box-shadow:inset 0 1px 2px #eee}
.btn{position:absolute;background:var(--green);color:#fff;font-family:'Open Sans',sans-serif;font-weight:600;font-size:11px;text-align:center;line-height:18px}
.client{position:absolute;top:1026px;font-family:'Open Sans',sans-serif;font-weight:700;font-size:16px;color:#666}
.foot{left:0;top:1084px;width:952px;height:116px;background:var(--foot)}
.fbox{position:absolute;top:1099px;height:57px;background:var(--footbox);border:1px solid #555;color:#fff;font-family:'Open Sans',sans-serif}
.fbox h4{font-size:11px;font-weight:600;margin:7px 0 0 9px}
.fin{position:absolute;left:7px;top:28px;width:136px;height:20px;background:#5a5a5a;font:italic 9px Arial,sans-serif;color:#ddd;padding:5px 8px}
.fgo{position:absolute;left:147px;top:28px;width:24px;height:20px;background:#5a5a5a}
.fline{font:9px Arial,sans-serif;margin:5px 0 0 9px;display:flex;align-items:center;gap:7px}
.soc{position:absolute;top:31px;width:19px;height:19px;border-radius:3px}
.links{left:140px;top:1176px;font-size:8.5px;color:#fff}
.links b{color:var(--green);font-weight:400}
.copyr{left:610px;top:1176px;font-size:8.5px;color:#fff}
</style>
</head>
<body>

<header class="head">
  <div class="brand" style="left:140px;top:32px"><i></i>Velmora Systems</div>
  <div class="abs search">search
    <svg width="11" height="11" viewBox="0 0 11 11"><circle cx="4.5" cy="4.5" r="3.5" fill="none" stroke="#888" stroke-width="1.4"/><line x1="7" y1="7" x2="10" y2="10" stroke="#888" stroke-width="1.6"/></svg>
  </div>
  <div class="abs call">
    <svg width="25" height="25" viewBox="0 0 25 25"><circle cx="12.5" cy="12.5" r="11" fill="none" stroke="#1aa84c" stroke-width="1.6"/><path d="M9 7c-1 1-1 3 1 6s4 5 6 5l1.5-1.5-2.5-2-1.3 1c-1-.6-2.6-2.4-3-3.5l1-1.2-1.8-2.6z" fill="#1aa84c"/></svg>
    <small>Call Us Today</small><b>123 456 7890</b>
  </div>
  <nav class="abs nav"><span>HOME</span><span>ABOUT US</span><span>SERVICES</span><span>SUPPORT</span><span>TESTIMONIALS</span><span>CLIENTS</span><span>CONTACT US</span></nav>
</header>

<section class="abs hero">
  <div class="hero-photo" role="img" aria-label="Photo of a smiling technician standing beside a server rack"></div>
  <div class="arrow" style="left:144px"><svg width="28" height="28"><path d="M16 8l-6 6 6 6" fill="none" stroke="#fff" stroke-width="1.5"/></svg></div>
  <div class="arrow" style="left:780px"><svg width="28" height="28"><path d="M12 8l6 6-6 6" fill="none" stroke="#fff" stroke-width="1.5"/></svg></div>
  <div class="dots"><i></i><i></i></div>
  <div class="caption">WE HAVE SPECIALISED ENGINEERS, TRAINED TO DO SPECIALISED WORK</div>
</section>

<h2 style="left:143px;top:458px">Our Services</h2>
<svg class="abs" style="left:781px;top:465px" width="30" height="12"><path d="M6 1l-5 5 5 5M22 1l5 5-5 5" fill="none" stroke="#777" stroke-width="1.2"/><path d="M22 1l5 5-5 5" fill="none" stroke="#1aa84c" stroke-width="1.2"/></svg>
<div class="rule" style="left:142px;top:480px;width:671px"></div>

<div class="svc on" style="left:132px"><h3>On-site Service</h3>
  <div class="ring"><svg width="48" height="48" viewBox="0 0 48 48"><g stroke="#1aa84c" stroke-width="6" stroke-linecap="round"><line x1="12" y1="36" x2="34" y2="14"/><line x1="14" y1="12" x2="36" y2="36"/></g><rect x="8" y="6" width="14" height="8" fill="#1aa84c" transform="rotate(45 15 10)"/><circle cx="36" cy="12" r="7" fill="#1aa84c"/><circle cx="39" cy="9" r="3" fill="#fff"/></svg></div>
  <p>Lorem ipsum dolor sit amet ummy nibh eui smod</p></div>
<div class="svc" style="left:271px"><h3>Remote Desktop</h3>
  <div class="ring"><svg width="50" height="44" viewBox="0 0 50 44"><rect x="3" y="5" width="28" height="20" fill="none" stroke="#555" stroke-width="3"/><line x1="17" y1="25" x2="17" y2="32" stroke="#555" stroke-width="3"/><line x1="10" y1="33" x2="24" y2="33" stroke="#555" stroke-width="3"/><circle cx="34" cy="26" r="12" fill="#f5f5f5" stroke="#555" stroke-width="3"/><path d="M30 22l-3 4 3 4M38 22l3 4-3 4" fill="none" stroke="#555" stroke-width="2"/></svg></div>
  <p>Lorem ipsum dolor sit amet ummy nibh eui smod</p></div>
<div class="svc" style="left:410px"><h3>Medical IT Service</h3>
  <div class="ring"><svg width="50" height="44" viewBox="0 0 50 44"><path d="M8 4v12a8 8 0 0016 0V4" fill="none" stroke="#555" stroke-width="3"/><path d="M16 24v8a6 6 0 0012 0v-6" fill="none" stroke="#555" stroke-width="3"/><circle cx="28" cy="24" r="4" fill="#555"/><circle cx="38" cy="12" r="7" fill="none" stroke="#555" stroke-width="4" stroke-dasharray="3 2"/></svg></div>
  <p>Lorem ipsum dolor sit amet ummy nibh eui smod</p></div>
<div class="svc" style="left:547px"><h3>Pharmacy IT</h3>
  <div class="ring"><svg width="50" height="44" viewBox="0 0 50 44"><rect x="4" y="4" width="34" height="26" fill="none" stroke="#444" stroke-width="3"/><path d="M8 24l7-9 6 6 7-9 6 6" fill="none" stroke="#444" stroke-width="2"/><circle cx="36" cy="30" r="7" fill="#f5f5f5" stroke="#444" stroke-width="3"/><line x1="41" y1="35" x2="47" y2="41" stroke="#444" stroke-width="4"/></svg></div>
  <p>Lorem ipsum dolor sit amet ummy nibh eui smod</p></div>
<div class="svc" style="left:686px"><h3>Website Design</h3>
  <div class="ring"><svg width="50" height="44" viewBox="0 0 50 44"><rect x="6" y="10" width="36" height="24" fill="none" stroke="#444" stroke-width="3"/><line x1="24" y1="34" x2="24" y2="39" stroke="#444" stroke-width="3"/><line x1="15" y1="40" x2="33" y2="40" stroke="#444" stroke-width="3"/><line x1="20" y1="26" x2="38" y2="6" stroke="#444" stroke-width="3"/><line x1="12" y1="29" x2="26" y2="29" stroke="#444" stroke-width="2"/></svg></div>
  <p>Lorem ipsum dolor sit amet ummy nibh eui smod</p></div>

<div class="rule" style="left:142px;top:698px;width:671px;border-top:1px solid #eee"></div>

<h2 style="left:140px;top:726px">About Velmora Systems</h2>
<div class="rule" style="left:140px;top:749px;width:203px"></div>
<div class="abs about-img" role="img" aria-label="Photo of a business team meeting around a table"></div>
<p class="copy" style="left:140px;top:858px;width:202px">Velmora Systems is an Adelaide based company with a single objective - to excel in the support and service of all computer and IT needs. We provide a high level of consulting services using the most experienced engineers at a reasonable and fair price. We believe in using a Business Value approach to every</p>
<div class="more" style="left:288px;top:937px">Read More »</div>

<h2 style="left:373px;top:726px">Client Testimonials</h2>
<div class="rule" style="left:372px;top:749px;width:208px"></div>
<div class="quote" style="top:762px"><b style="font-size:13px">“</b> Nonummy nibh uismod tincidunt ut laoreet dolore magna aliquam erat volutpat. Ut wisi enim ad minim nonummy nibh euismod tincidunt <b style="font-size:13px">”</b><div class="by">Daniel Harwick - Orrin Data</div></div>
<div class="quote" style="top:824px"><b style="font-size:13px">“</b> I have always found the team extremely helpful with their advice over the phone. They also have the ability to access our computers remotely, and can rectify most problems quite swiftly. I have no hesitation in recommending Velmora Systems for all of your IT needs. <b style="font-size:13px">”</b><div class="by">Marcus Teller B.Pharm<br>Greenhill Community Pharmacy, Lyndale</div></div>
<div class="more" style="left:529px;top:937px">Read More »</div>

<h2 style="left:608px;top:726px">Quick Contact</h2>
<div class="rule" style="left:607px;top:749px;width:205px"></div>
<div class="field" style="top:760px">Name</div>
<div class="field" style="top:792px">Email</div>
<div class="field" style="top:824px">Phone</div>
<div class="field" style="top:857px;height:60px">Message</div>
<div class="btn" style="left:610px;top:929px;width:50px">Submit</div>

<h2 style="left:140px;top:979px">Our Clients</h2>
<svg class="abs" style="left:555px;top:985px" width="30" height="12"><path d="M6 1l-5 5 5 5" fill="none" stroke="#777" stroke-width="1.2"/><path d="M22 1l5 5-5 5" fill="none" stroke="#1aa84c" stroke-width="1.2"/></svg>
<div class="rule" style="left:140px;top:1002px;width:447px"></div>
<div class="client" style="left:140px">Northwind</div>
<div class="client" style="left:278px">Cloudpeak</div>
<div class="client" style="left:420px">Arvion</div>
<div class="client" style="left:510px">Kestrel</div>

<h2 style="left:604px;top:979px">Remote Support</h2>
<div class="rule" style="left:604px;top:1002px;width:206px"></div>
<div class="field" style="left:604px;top:1012px;width:203px">Enter your 6 digit code</div>
<div class="btn" style="left:605px;top:1040px;width:72px">Connect Now</div>

<footer class="abs foot"></footer>
<div class="fbox" style="left:140px;width:183px"><h4>Subscribe to Newsletter</h4><div class="fin">Email here</div><div class="fgo"><svg width="24" height="20"><path d="M10 5l5 5-5 5" fill="none" stroke="#fff" stroke-width="2"/></svg></div></div>
<div class="fbox" style="left:363px;width:161px"><h4>Contact Us</h4>
  <div class="fline"><svg width="8" height="8"><path d="M1 1c0 3 3 6 6 6l1-1-2-2-1 1C4 4 3 3 3 3l1-1-2-2z" fill="#fff"/></svg>123 456 7890</div>
  <div class="fline" style="margin-top:2px"><svg width="9" height="7"><rect x=".5" y=".5" width="8" height="6" fill="none" stroke="#fff"/><path d="M.5 .5l4 3 4-3" fill="none" stroke="#fff"/></svg>support@velmorasystems.example</div></div>
<div class="fbox" style="left:564px;width:88px"><h4>Follow Us</h4>
  <div class="soc" style="left:6px;background:#3a5a98"></div><div class="soc" style="left:35px;background:#3fa9e0"></div><div class="soc" style="left:64px;background:#e8741c"></div></div>
<div class="abs" style="left:692px;top:1097px;width:119px;height:60px;background:var(--green);display:flex;align-items:center;justify-content:center;gap:6px;font-family:'Open Sans',sans-serif;font-weight:700;font-size:13px;color:#fff"><i style="display:block;width:14px;height:14px;background:#fff"></i>Velmora Systems</div>
<div class="abs links"><b>Home</b> &nbsp;| &nbsp;About Us &nbsp;| &nbsp;Services | &nbsp;Support &nbsp;| &nbsp;Testimonials &nbsp;| &nbsp;Clients &nbsp;| &nbsp;Contact Us &nbsp;| &nbsp;Terms Conditions</div>
<div class="abs copyr">Copyright © 2014 &nbsp;velmorasystems. &nbsp;All Rights Reserved</div>

</body>
</html>
```